SaaS Early tech startup business card design

Unique design for experience ecommerce platform company. the business cards will be used by executive members. conformance with color code is required.

```html
<!DOCTYPE html>
<html lang="en">
<head>
<meta charset="utf-8">
<title>novari business card</title>
<link href="https://fonts.googleapis.com/css2?family=Roboto:wght@400;500;700&display=swap" rel="stylesheet">
<style>
  :root {
    --backdrop: #6b6768;
    --navy: #1f2237;
    --paper: #f4f4f4;
    --teal: #17a596;
    --teal-deep: #0f6f78;
    --ocean: #1c6a8c;
    --ink: #2a2a2a;
    --white: #ffffff;
  }
  * { margin: 0; padding: 0; box-sizing: border-box; }
  html, body { width: 1200px; height: 1200px; overflow: hidden; }
  body {
    background: var(--backdrop);
    font-family: "Roboto", sans-serif;
    position: relative;
  }
  .card {
    position: absolute;
    width: 592px;
    height: 348px;
    border-radius: 22px;
    overflow: hidden;
  }
  .card--front { left: 300px; top: 198px; background: var(--navy); }
  .card--back { left: 294px; top: 637px; background: var(--paper); }

  .brand { position: absolute; text-align: left; }
  .brand__name {
    font-family: "Roboto", sans-serif;
    font-weight: 700;
    font-size: 82px;
    line-height: 1;
    letter-spacing: -1px;
    color: var(--teal);
  }
  .brand__tagline {
    font-family: "Roboto", sans-serif;
    font-weight: 400;
    font-size: 14px;
    letter-spacing: 6.2px;
    margin-top: 10px;
    white-space: nowrap;
  }
  .card--front .brand { left: 58px; top: 124px; }
  .card--front .brand__tagline { color: var(--white); }
  .card--back .brand { left: 74px; top: 126px; }
  .card--back .brand__tagline { color: var(--teal); font-size: 13px; letter-spacing: 5.6px; padding-left: 8px; }

  .accent-field { position: absolute; }
  .card--front .accent-field {
    right: 0; top: 0; width: 268px; height: 348px;
    background: linear-gradient(200deg, rgba(28,106,140,0.45) 0%, rgba(23,165,150,0.35) 55%, rgba(31,34,55,0) 100%);
  }
  .card--back .accent-field {
    left: 0; bottom: 0; width: 108px; height: 108px;
    background: linear-gradient(30deg, rgba(23,165,150,0.22) 0%, rgba(28,106,140,0.12) 60%, rgba(244,244,244,0) 100%);
  }

  .contact { position: absolute; left: 353px; top: 80px; color: var(--ink); }
  .contact__name {
    font-weight: 700;
    font-size: 23px;
    color: var(--teal-deep);
    letter-spacing: -0.3px;
  }
  .contact__role { font-size: 15px; margin-top: 2px; }
  .contact__list { list-style: none; margin-top: 24px; }
  .contact__item {
    display: flex; align-items: center;
    font-size: 15.5px; height: 22.5px;
  }
  .contact__icon { width: 14px; height: 14px; margin-right: 17px; fill: var(--teal-deep); }
  .contact__address { font-size: 15.5px; line-height: 22.5px; margin-top: 5px; }
</style>
</head>
<body>
  <section class="card card--front">
    <div class="accent-field" role="img" aria-label="Faint layered ribbon pattern in blue and teal"></div>
    <div class="brand">
      <div class="brand__name">novari</div>
      <div class="brand__tagline">MADE AROUND YOU</div>
    </div>
  </section>

  <section class="card card--back">
    <div class="accent-field" role="img" aria-label="Faint layered ribbon pattern in pale teal"></div>
    <div class="brand">
      <div class="brand__name">novari</div>
      <div class="brand__tagline">MADE AROUND YOU</div>
    </div>
    <div class="contact">
      <div class="contact__name">Karim D.</div>
      <div class="contact__role">CTO/Owner</div>
      <ul class="contact__list">
        <li class="contact__item">
          <svg class="contact__icon" viewBox="0 0 16 16"><path d="M2 6c0-2 3-3.5 6-3.5S14 4 14 6l-3 .6-.6-1.6H5.6L5 6.6z"/><path d="M4 8h8l1 5H3z"/></svg>
          (00) 0111 NOVA
        </li>
        <li class="contact__item">
          <svg class="contact__icon" viewBox="0 0 16 16"><path d="M1 3h14v10H1z M2.5 4.5 8 9l5.5-4.5" fill-rule="evenodd"/></svg>
          hello@novari.net
        </li>
        <li class="contact__item">
          <svg class="contact__icon" viewBox="0 0 16 16"><circle cx="8" cy="8" r="6.5"/><path d="M1.5 8h13M8 1.5v13" stroke="#f4f4f4" stroke-width="1.2" fill="none"/></svg>
          www.novari.net
        </li>
      </ul>
      <p class="contact__address">Harbor Point, Dubai<br>Dubai Media Quarter, UAE</p>
    </div>
  </section>
</body>
</html>
```